Industry / Entity Type

Financial consultancy / advisers

Current site is: http://www.brightmoor-counsel.com

Looking for a complete overhaul of this site, we are after a clean modern look. Will require the ability to easily add, update and remove content, hence the WordPress design.
Example:
Add case studies
Industry documentation (downloadable brochures / flyers and such)

What we like from our current site is the colour the fonts and the logo (the city of London) we would like to have other city outlines (NYC and Tokyo, Hong Kong, Singapore).

The site will be used by our potential clients to get in contact and re-view the case studies, if possible would like to have a client login area where they can download our documents like NDA’s etc and T&C’s.

Task Outline

Create a Web Design (Coded - Design and coding required)
Designer must provide full implementation/coding depending on the platform chosen by the client (i.e. WordPress theme, HTML/CSS, bootstrap etc.)

Task Description

I need a full website built that must work on desktop and mobile. I can provide the London city skyline and the font file, which we have used. Some stock industrial photos will be required.

Requirements:

*Splash page
*What We Do
*How We do it
*Who Are We? To have the same information and links as the current site
*Why use us?
*Clients: To have the same information and links as the current site
*Partners: To have the same information and links as the current site
*Contact:

Target Market(s)

Financial institutions trading Equities, Futures, Options, Forex and Fixed Income.
Regulators, Exchanges, ECN’s
Buy side firms and Sell side firms

Industry/Entity Type

Financial

Coding

Coded - Design and coding required

Number of Pages Required

5+ page

Font styles to use
Sans Serif

Colors
f04a50

Requirements
Must have
• Splash page
• What We Do
• How We do it
• Who Are We? To have the same information and links as the current site
• Why use us?
• Clients: To have the same information and links as the current site
• Partners: To have the same information and links as the current site
• Contact:

```html
<!DOCTYPE html>
<html lang="en">
<head>
<meta charset="utf-8">
<title>Brightmoor Counsel</title>
<link href="https://fonts.googleapis.com/css2?family=Questrial&family=Open+Sans:wght@400;600&display=swap" rel="stylesheet">
<style>
:root{
  --brand:#f04a50;
  --white:#ffffff;
  --ink:#333333;
  --muted:#8a8a8a;
  --nav:#555555;
  --panel:#f1f1f1;
  --footer:#2b2b2b;
  --footer-text:#c9c9c9;
  --hero-a:#d9d6d4;
  --hero-b:#a59d98;
}
*{box-sizing:border-box;margin:0;padding:0}
html,body{width:935px;height:1200px;overflow:hidden;background:var(--white)}
body{position:relative;font-family:"Open Sans",Arial,sans-serif;color:var(--ink)}
.header{position:absolute;left:0;top:0;width:935px;height:125px;background:var(--brand)}
.brand-name{position:absolute;left:102px;top:42px;width:265px;text-align:center;color:var(--white);font-family:"Questrial",Arial,sans-serif;font-size:21px;letter-spacing:3px;text-transform:uppercase;line-height:26px}
.login{position:absolute;left:768px;top:20px;width:64px;height:30px;border:1px solid var(--white);border-radius:2px;color:var(--white);font-size:10px;display:flex;align-items:center;justify-content:center;gap:4px}
.contact-line{position:absolute;right:103px;color:var(--white);font-family:"Questrial",Arial,sans-serif;display:flex;align-items:center;gap:5px}
.contact-email{top:71px;font-size:10px;text-transform:uppercase}
.contact-phone{top:87px;font-size:14px}
.nav{position:absolute;left:0;top:125px;width:935px;height:42px;display:flex;align-items:center;font-family:"Questrial",Arial,sans-serif;font-size:10px;text-transform:uppercase;color:var(--nav)}
.nav span{position:absolute}
.nav .active{color:var(--brand)}
.hero{position:absolute;left:0;top:167px;width:935px;height:312px;background:linear-gradient(100deg,var(--hero-a) 0%,#ece9e7 35%,var(--hero-b) 75%,#6e625c 100%)}
.hero-arrow{position:absolute;top:143px;width:19px;height:25px;background:rgba(120,120,120,.55);display:flex;align-items:center;justify-content:center}
.intro{position:absolute;left:102px;top:524px;width:731px;text-align:center;font-size:8.6px;line-height:16.4px;color:var(--ink)}
.service{position:absolute;width:160px;text-align:center}
.service .badge{width:62px;height:62px;border-radius:50%;background:var(--brand);margin:0 auto;display:flex;align-items:center;justify-content:center}
.service h3{font-family:"Questrial",Arial,sans-serif;font-weight:400;font-size:12.5px;font-variant:small-caps;letter-spacing:.5px;margin-top:9px;color:var(--ink);text-transform:capitalize}
.service p{font-size:7.6px;line-height:12.3px;color:var(--muted);margin-top:3px}
.skyline{position:absolute;left:0;top:940px;width:935px;height:54px;background:linear-gradient(180deg,var(--white) 0%,#f6f6f6 100%);border-bottom:1px solid #d6d6d6}
.clients{position:absolute;left:0;top:994px;width:935px;height:131px;background:var(--panel)}
.tabs{position:absolute;top:30px;width:935px;text-align:center;font-family:"Questrial",Arial,sans-serif;font-size:11px;font-variant:small-caps;letter-spacing:.5px;color:var(--ink)}
.tabs .active{color:var(--brand)}
.tabs .sep{margin:0 8px}
.client-row{position:absolute;top:70px;left:95px;width:745px;display:flex;justify-content:space-between;align-items:center}
.client-name{font-family:"Questrial",Arial,sans-serif;font-size:15px;color:#555555;display:flex;align-items:center;gap:5px}
.client-name i{width:10px;height:10px;border-radius:50%;background:#555555;display:inline-block}
.client-arrow{position:absolute;top:56px}
.footer{position:absolute;left:0;top:1125px;width:935px;height:75px;background:var(--footer);color:var(--footer-text);font-size:8px}
.footer-links{position:absolute;left:103px;top:22px}
.footer-links span{margin:0 5px}
.footer-links span:first-child{margin-left:0}
.copyright{position:absolute;left:103px;top:43px}
.social{position:absolute;top:28px;width:19px;height:19px;border-radius:50%}
</style>
</head>
<body>
<header class="header">
  <div class="brand-name">Brightmoor<br>Counsel</div>
  <div class="login">
    <svg width="9" height="9" viewBox="0 0 10 10"><path d="M1 4h4V2l3 3-3 3V6H1z" fill="#fff"/><path d="M6 1h3v8H6" stroke="#fff" fill="none"/></svg>Log in
  </div>
  <div class="contact-line contact-email">sales@brightmoor-counsel.com
    <svg width="9" height="7" viewBox="0 0 9 7"><rect width="9" height="7" fill="#fff"/><path d="M0 0l4.5 4L9 0" stroke="#f04a50" fill="none"/></svg>
  </div>
  <div class="contact-line contact-phone">+44(0)20 7946 0381
    <svg width="10" height="10" viewBox="0 0 10 10"><path d="M2 0l2 2.5-1 1.2c.6 1.3 1.6 2.3 2.9 2.9l1.2-1L9.6 8 8.3 9.6C4 9.3.7 6 .4 1.7z" fill="#fff"/></svg>
  </div>
</header>

<nav class="nav">
  <span class="active" style="left:108px">Home</span>
  <span style="left:177px">What we do</span>
  <span style="left:282px">How we do it</span>
  <span style="left:394px">Who are we</span>
  <span style="left:500px">Why use us</span>
  <span style="left:601px">Clients</span>
  <span style="left:683px">Partners</span>
  <span style="left:776px">Contact</span>
</nav>

<section class="hero" role="img" aria-label="Photo of a hand holding a pen over a calculator beside a laptop on an office desk">
  <div class="hero-arrow" style="left:0"><svg width="8" height="14"><path d="M7 1L1 7l6 6" stroke="#fff" fill="none"/></svg></div>
  <div class="hero-arrow" style="right:0"><svg width="8" height="14"><path d="M1 1l6 6-6 6" stroke="#fff" fill="none"/></svg></div>
</section>

<p class="intro">Since founding Brightmoor Counsel in 2014 we have dedicated ourselves to the provision of services. What differentiates us from other advisers or consultancies is a genuine motivation to see our clients succeed. Today's technology allows our clients to take their knowledge to the market in ways that previous generations could only dream of. That's why BMC is dedicated to seeing you choose the right technology strategy, ensuring you maintain a competitive edge over your peers.</p>

<div class="service" style="left:114px;top:602px">
  <div class="badge"><svg width="22" height="26" viewBox="0 0 22 26"><path d="M11 2a8 8 0 0 0-5 14c1 1 1.5 2 1.5 3h7c0-1 .5-2 1.5-3a8 8 0 0 0-5-14z" stroke="#fff" stroke-width="2" fill="none"/><rect x="7.5" y="21" width="7" height="2" fill="#fff"/><rect x="8.5" y="24" width="5" height="2" fill="#fff"/></svg></div>
  <h3>Advice</h3>
  <p>Donec non eros sodales, tristique odio sed, pellentesque libero. Morbi neque sit amet massa.</p>
</div>
<div class="service" style="left:299px;top:602px">
  <div class="badge"><svg width="28" height="24" viewBox="0 0 28 24"><circle cx="9" cy="13" r="6" stroke="#fff" stroke-width="4" stroke-dasharray="3 2" fill="none"/><circle cx="9" cy="13" r="2" fill="#fff"/><circle cx="21" cy="7" r="4" stroke="#fff" stroke-width="3" stroke-dasharray="2 1.5" fill="none"/><circle cx="21" cy="18" r="3.5" stroke="#fff" stroke-width="3" stroke-dasharray="2 1.5" fill="none"/></svg></div>
  <h3>Product Development</h3>
  <p>Donec non eros sodales, tristique odio sed, pellentesque libero. Morbi neque sit amet massa.</p>
</div>
<div class="service" style="left:485px;top:602px">
  <div class="badge"><svg width="28" height="22" viewBox="0 0 28 22"><circle cx="14" cy="5" r="4" fill="#fff"/><circle cx="6" cy="7" r="3" fill="#fff"/><circle cx="22" cy="7" r="3" fill="#fff"/><path d="M7 20c0-6 3-9 7-9s7 3 7 9z" fill="#fff"/><path d="M0 18c0-5 2-7 5-7l1 7zM28 18c0-5-2-7-5-7l-1 7z" fill="#fff"/></svg></div>
  <h3>Interim Management</h3>
  <p>Donec non eros sodales, tristique odio sed, pellentesque libero. Morbi neque sit amet massa.</p>
</div>
<div class="service" style="left:671px;top:602px">
  <div class="badge"><svg width="26" height="26" viewBox="0 0 26 26"><circle cx="13" cy="13" r="12" fill="#fff"/><path d="M6 7c3-1 5 1 6 3s-1 3-3 3-2 3-4 2-1-6 1-8zM15 15c2 0 4 1 3 4s-3 3-4 1 0-5 1-5z" fill="#f04a50"/></svg></div>
  <h3>Process Outsourcing</h3>
  <p>Donec non eros sodales, tristique odio sed, pellentesque libero. Morbi neque sit amet massa.</p>
</div>

<div class="service" style="left:201px;top:758px">
  <div class="badge"><svg width="28" height="22" viewBox="0 0 28 22"><path d="M1 1v20h26" stroke="#fff" stroke-width="2" fill="none"/><rect x="5" y="12" width="3" height="7" fill="#fff"/><rect x="10" y="7" width="3" height="12" fill="#fff"/><rect x="15" y="10" width="3" height="9" fill="#fff"/><rect x="20" y="4" width="3" height="15" fill="#fff"/></svg></div>
  <h3>Research</h3>
  <p>Donec non eros sodales, tristique odio sed, pellentesque libero. Morbi neque sit amet massa.</p>
</div>
<div class="service" style="left:387px;top:758px">
  <div class="badge"><svg width="26" height="24" viewBox="0 0 26 24"><path d="M7 1h18l-5 18H2z" fill="#fff"/><path d="M2 19h18l-1 4H3c-2 0-2-4-1-4z" stroke="#fff" stroke-width="1.5" fill="none"/><path d="M10 6h10M9 10h10" stroke="#f04a50" stroke-width="1.5"/></svg></div>
  <h3>Training</h3>
  <p>Donec non eros sodales, tristique odio sed, pellentesque libero. Morbi neque sit amet massa.</p>
</div>
<div class="service" style="left:572px;top:758px">
  <div class="badge"><svg width="22" height="26" viewBox="0 0 22 26"><path d="M1 1h20v12c0 6-5 10-10 12C6 23 1 19 1 13z" fill="#fff"/><path d="M7 5h8v8c0 3-2 5-4 6-2-1-4-3-4-6z" fill="#f04a50"/></svg></div>
  <h3>MiFID II</h3>
  <p>Donec non eros sodales, tristique odio sed, pellentesque libero. Morbi neque sit amet massa.</p>
</div>

<div class="skyline" role="img" aria-label="Thin outline drawing of a city skyline running across the page"></div>

<section class="clients">
  <div class="tabs"><span class="active">Clients</span><span class="sep">|</span><span>Partners</span></div>
  <svg class="client-arrow" style="left:18px" width="12" height="20"><path d="M10 1L2 10l8 9" stroke="#999" stroke-width="1.5" fill="none"/></svg>
  <svg class="client-arrow" style="right:18px" width="12" height="20"><path d="M2 1l8 9-8 9" stroke="#999" stroke-width="1.5" fill="none"/></svg>
  <div class="client-row">
    <span class="client-name"><i></i>Tessel</span>
    <span class="client-name">Marrow</span>
    <span class="client-name">Quillan</span>
    <span class="client-name">Ashford</span>
    <span class="client-name">Lumen</span>
    <span class="client-name">Norvia</span>
    <span class="client-name">Halden</span>
  </div>
</section>

<footer class="footer">
  <div class="footer-links"><span>Home</span>|<span>What we do</span>|<span>How we do it</span>|<span>Who are we</span>|<span>Why use us</span>|<span>Clients</span>|<span>Partners</span>|<span>Contact</span></div>
  <div class="copyright">Copyright &copy; 2017 &nbsp;Company name. &nbsp;All rights reserved.</div>
  <div class="social" style="left:786px;background:#3b5998"></div>
  <div class="social" style="left:812px;background:#2aa3ef"></div>
</footer>
</body>
</html>
```